Business Card Design (NEW FILES)

ATTENTION: New vector files are available. Please update your design to reflect/use the new (better resolution) logo images.

Seeking a unique and professional business card design for a commercial drone photography/videography business. The layout should feature
the logo (attached) and include the following information:
Owen Tarrick
614-502-7738
www.skylarkreelworks.example
NRD Certified Remote Pilot

Owen Tarrick

```html
<!DOCTYPE html>
<html lang="en">
<head>
<meta charset="utf-8">
<title>Skylark Reelworks – Business Card</title>
<link rel="stylesheet" href="https://fonts.googleapis.com/css2?family=Open+Sans:wght@400;600;700;800&display=swap">
<style>
  :root {
    --stage: #232323;
    --navy: #161a48;
    --navy-light: #2a3a9a;
    --orange: #ee8a44;
    --white: #ffffff;
    --ink: #161a48;
  }
  * { box-sizing: border-box; margin: 0; padding: 0; }
  html, body { width: 1200px; height: 780px; overflow: hidden; background: var(--stage); }
  body { position: relative; font-family: "Open Sans", Arial, sans-serif; }

  .card {
    position: absolute;
    top: 75px;
    width: 360px;
    height: 630px;
    border-radius: 24px;
    overflow: hidden;
    box-shadow: 0 14px 30px rgba(0,0,0,.5);
  }

  /* Back side */
  .card-back { left: 190px; background: var(--navy); }
  .back-decoration {
    position: absolute; inset: 0;
    background: radial-gradient(ellipse at 40% 42%, rgba(42,58,154,.55) 0%, rgba(42,58,154,.18) 45%, rgba(22,26,72,0) 75%);
  }
  .back-brand {
    position: absolute; left: 0; right: 0; top: 420px;
    text-align: center;
  }
  .back-brand .brand-name { color: var(--white); font-size: 26px; }
  .brand-mark {
    display: inline-block; width: 14px; height: 14px; border-radius: 50%;
    background: var(--orange); margin-right: 8px; vertical-align: middle;
  }

  /* Front side */
  .card-front { left: 650px; background: var(--white); }
  .front-brand { position: absolute; left: 0; right: 0; top: 70px; text-align: center; }
  .brand-name {
    font-weight: 700; color: var(--ink); font-size: 24px; letter-spacing: .5px;
    vertical-align: middle;
  }

  .contact-block { position: absolute; left: 0; right: 0; top: 330px; text-align: center; color: var(--ink); }
  .person-name { font-size: 34px; font-weight: 800; line-height: 1.1; }
  .person-name .first { color: var(--orange); }
  .person-name .last { color: var(--ink); }
  .person-role { font-size: 15px; font-weight: 700; margin-top: 2px; }

  .icon-row {
    display: flex; align-items: center; justify-content: center; gap: 8px; margin-top: 10px;
  }
  .icon-row .rule { width: 70px; height: 2px; background: var(--orange); }
  .icon-row svg { width: 26px; height: 26px; display: block; }

  .contact-line { font-size: 15px; font-weight: 600; margin-top: 8px; }
  .contact-line + .contact-line { margin-top: 2px; }

  .credentials { position: absolute; left: 40px; right: 40px; top: 510px; text-align: center; color: var(--ink); }
  .credentials .rule { height: 2px; background: var(--orange); margin-bottom: 12px; }
  .credentials p { font-size: 15px; font-weight: 600; line-height: 1.35; }
</style>
</head>
<body>

  <section class="card card-back">
    <div class="back-decoration" role="img" aria-label="Large embossed brand emblem decoration in deep blue tones"></div>
    <div class="back-brand">
      <span class="brand-mark"></span><span class="brand-name">Skylark Reelworks</span>
    </div>
  </section>

  <section class="card card-front">
    <div class="front-brand">
      <span class="brand-mark"></span><span class="brand-name">Skylark Reelworks</span>
    </div>

    <div class="contact-block">
      <h1 class="person-name"><span class="first">Owen</span> <span class="last">Tarrick</span></h1>
      <p class="person-role">Owner</p>

      <div class="icon-row">
        <span class="rule"></span>
        <svg viewBox="0 0 26 26" aria-label="Phone">
          <polygon points="13,1 24,7 24,19 13,25 2,19 2,7" fill="#ee8a44"/>
          <path d="M9 8c1-.6 1.6-.4 2 .4l.8 1.6c.3.6.1 1-.4 1.4l-.6.5c.6 1.4 1.6 2.4 3 3l.5-.6c.4-.5.8-.7 1.4-.4l1.6.8c.8.4 1 1 .4 2-.8 1.2-2 1.5-3.4.8-2.6-1.2-4.4-3-5.6-5.6C8 10.6 8 9.4 9 8z" fill="#fff"/>
        </svg>
        <svg viewBox="0 0 26 26" aria-label="Website">
          <polygon points="13,1 24,7 24,19 13,25 2,19 2,7" fill="#ee8a44"/>
          <circle cx="13" cy="13" r="6" fill="none" stroke="#fff" stroke-width="1.5"/>
          <ellipse cx="13" cy="13" rx="2.5" ry="6" fill="none" stroke="#fff" stroke-width="1.2"/>
          <line x1="7" y1="13" x2="19" y2="13" stroke="#fff" stroke-width="1.2"/>
        </svg>
        <span class="rule"></span>
      </div>

      <p class="contact-line">614-502-7738</p>
      <p class="contact-line">www.skylarkreelworks.example</p>
    </div>

    <div class="credentials">
      <div class="rule"></div>
      <p>NRD Certified Remote Pilot</p>
      <p>Fully Insured</p>
    </div>
  </section>

</body>
</html>
```